Business card for event manager / organizer "waiter service"

Draft of a new valuable business card for my company.
Events, personnel service providers, festivals

```html
<!DOCTYPE html>
<html lang="de">
<head>
<meta charset="utf-8">
<title>BERKO Kellnerservice – Visitenkarte</title>
<link href="https://fonts.googleapis.com/css2?family=Poppins:ital,wght@0,400;0,500;1,400&display=swap" rel="stylesheet">
<style>
  :root {
    --stage: #2c2c2d;
    --card: #070707;
    --orange: #e57e1c;
    --orange-deep: #9a5519;
    --white: #ffffff;
    --muted: #d9d9d9;
  }
  * { box-sizing: border-box; margin: 0; padding: 0; }
  html, body { width: 1093px; height: 1200px; overflow: hidden; }
  body {
    background: var(--stage);
    font-family: "Poppins", sans-serif;
    color: var(--white);
    position: relative;
  }
  .card {
    position: absolute;
    left: 265px;
    width: 580px;
    height: 357px;
    background: var(--card);
    border-radius: 26px;
    overflow: hidden;
    box-shadow: 0 6px 14px rgba(0,0,0,.55);
  }
  .card--front { top: 226px; }
  .card--back { top: 621px; }

  /* Front */
  .portrait {
    position: absolute;
    left: 0; top: 30px;
    width: 260px; height: 327px;
    background: radial-gradient(ellipse at 40% 55%, #8a8a8e 0%, #3b3b3e 45%, #070707 78%);
  }
  .details { position: absolute; left: 251px; top: 78px; width: 320px; }
  .name {
    color: var(--orange);
    font-weight: 500;
    font-size: 20px;
    line-height: 22px;
    letter-spacing: .2px;
  }
  .role { font-size: 16px; line-height: 20px; color: var(--white); }
  .rule { width: 60px; height: 1px; background: var(--orange); margin: 12px 0 19px; }
  .contact-list { list-style: none; }
  .contact-list li {
    display: flex; align-items: center; gap: 6px;
    font-size: 15.5px; line-height: 19.5px;
  }
  .contact-list svg { width: 14px; height: 14px; flex: none; fill: var(--orange); }
  .rule--lower { margin: 16px 0 20px; }
  .contact-list .social { font-style: italic; font-size: 14px; margin-top: 5px; }
  .social-dot { width: 10px; height: 10px; border-radius: 50%; background: var(--orange); margin: 0 2px; flex: none; }

  /* Back */
  .brand {
    position: absolute; top: 56px; left: 0; width: 100%;
    display: flex; flex-direction: column; align-items: center;
  }
  .brand-line { display: flex; align-items: center; gap: 10px; }
  .brand-mark { width: 34px; height: 34px; background: var(--orange); }
  .brand-name { font-weight: 500; font-size: 26px; line-height: 30px; color: var(--white); }
  .brand-tagline { font-size: 8px; color: var(--muted); margin-top: 6px; margin-left: 60px; }
  .gallery { position: absolute; top: 156px; left: 46px; display: flex; gap: 13px; }
  .gallery-item {
    width: 155px; height: 120px;
    border: 1.5px solid #e8e8e8;
  }
  .gallery-item--wedding { background: linear-gradient(135deg, #6b6fa6, #d9c7c2 50%, #8d6d58); }
  .gallery-item--waiter { background: radial-gradient(circle at 50% 40%, #e6e6e6, #5a5a5a 70%, #2a2a2a); }
  .gallery-item--concert { background: linear-gradient(180deg, #b47be0 0%, #6a2a8f 45%, #150818 80%); }
  .services {
    position: absolute; left: 0; bottom: 0; width: 100%; height: 57px;
    background: linear-gradient(180deg, var(--orange) 0%, var(--orange-deep) 100%);
    display: flex; align-items: center; justify-content: center;
    font-size: 20px; color: var(--white);
  }
</style>
</head>
<body>

<section class="card card--front">
  <div class="portrait" role="img" aria-label="Portrait photo of the owner in white shirt and black waistcoat, arms crossed"></div>
  <div class="details">
    <h1 class="name">JONAS BERKHOLT</h1>
    <p class="role">Inhaber</p>
    <div class="rule"></div>
    <ul class="contact-list">
      <li><svg viewBox="0 0 24 24"><path d="M6.6 10.8a15 15 0 0 0 6.6 6.6l2.2-2.2c.3-.3.7-.4 1-.2 1.1.4 2.3.6 3.6.6.6 0 1 .4 1 1V20c0 .6-.4 1-1 1A17 17 0 0 1 3 4c0-.6.4-1 1-1h3.5c.6 0 1 .4 1 1 0 1.3.2 2.5.6 3.6.1.3 0 .7-.2 1z"/></svg>02361 482 17 30</li>
      <li><svg viewBox="0 0 24 24"><path d="M6.6 10.8a15 15 0 0 0 6.6 6.6l2.2-2.2c.3-.3.7-.4 1-.2 1.1.4 2.3.6 3.6.6.6 0 1 .4 1 1V20c0 .6-.4 1-1 1A17 17 0 0 1 3 4c0-.6.4-1 1-1h3.5c.6 0 1 .4 1 1 0 1.3.2 2.5.6 3.6.1.3 0 .7-.2 1z"/></svg>0171 264 83 19</li>
      <li><svg viewBox="0 0 24 24"><path d="M12 2a10 10 0 1 0 0 20 10 10 0 0 0 0-20zm6.9 6h-3a15.6 15.6 0 0 0-1.3-3.6A8 8 0 0 1 18.9 8zM12 4c.8 1.2 1.5 2.5 1.9 4h-3.8c.4-1.5 1.1-2.8 1.9-4zM4.3 14a8.2 8.2 0 0 1 0-4h3.4a16 16 0 0 0 0 4zm.8 2h3a15.6 15.6 0 0 0 1.3 3.6A8 8 0 0 1 5.1 16zm3-8h-3a8 8 0 0 1 4.3-3.6C8.8 5.5 8.4 6.7 8.1 8zM12 20c-.8-1.2-1.5-2.5-1.9-4h3.8c-.4 1.5-1.1 2.8-1.9 4zm2.3-6H9.7a14.7 14.7 0 0 1 0-4h4.6a14.7 14.7 0 0 1 0 4zm.3 5.6c.6-1.1 1-2.3 1.3-3.6h3a8 8 0 0 1-4.3 3.6zm1.7-5.6a16 16 0 0 0 0-4h3.4a8.2 8.2 0 0 1 0 4z"/></svg>www.berko-kellnerservice.de</li>
      <li><svg viewBox="0 0 24 24"><path d="M2 5h20v14H2zm2 2v.4l8 5.2 8-5.2V7zm0 2.8V17h16V9.8l-8 5.2z"/></svg>kontakt@berko-kellnerservice.de</li>
    </ul>
    <div class="rule rule--lower"></div>
    <ul class="contact-list">
      <li><svg viewBox="0 0 24 24"><path d="M12 2a7 7 0 0 0-7 7c0 5.2 7 13 7 13s7-7.8 7-13a7 7 0 0 0-7-7zm0 9.5a2.5 2.5 0 1 1 0-5 2.5 2.5 0 0 1 0 5z"/></svg>Birkenweg 14, 45657 Lindhorst</li>
      <li class="social"><span class="social-dot"></span>social: berkokellnerservice</li>
    </ul>
  </div>
</section>

<section class="card card--back">
  <div class="brand">
    <div class="brand-line">
      <span class="brand-mark"></span>
      <span class="brand-name">BERKO Kellnerservice</span>
    </div>
    <p class="brand-tagline">...denn die nächste Feier kommt bestimmt!</p>
  </div>
  <div class="gallery">
    <div class="gallery-item gallery-item--wedding" role="img" aria-label="Photo of a wedding couple dancing under confetti and sparklers"></div>
    <div class="gallery-item gallery-item--waiter" role="img" aria-label="Photo of a waiter in bow tie holding champagne glasses"></div>
    <div class="gallery-item gallery-item--concert" role="img" aria-label="Photo of a festival crowd under purple stage lights"></div>
  </div>
  <div class="services">Events | Personnel Service Providers | Festivals</div>
</section>

</body>
</html>
```